Business Card for beauty technology startup

Design Glimora Business Card for a Beauty, based on the website identity and colors (https://www.glimora-example.com).
Glimora is a beauty tech startup that gathers helpful product info for beauty lovers and consumers (such as availability on stores, price range and product reviews) for makeup products. The card design must be young, colorful but clean, and very modern.

Target Market(s)

woman, 15-35

Industry/Entity Type

Cosmetics

Contact Information for Business Card

Full Name, address, phone

Font styles to use
Other font styles liked:
• Advent Pro

Colors
e34297
86cfc6
ffffff
5c5c5c
e8e8e8
e667a6
b2b2b2

Requirements
Must have
• One full colored side with a creative design and another with card info
• Use Color palette: #95C5C5 and/or #D38AA5
• Use fonts: Advent Pro
• Use website identity: https://www.glimora-example.com
Nice to have
• If needed extra font: Roboto

```html
<!DOCTYPE html>
<html lang="en">
<head>
<meta charset="utf-8">
<title>Glimora Business Card</title>
<link rel="stylesheet" href="https://fonts.googleapis.com/css2?family=Advent+Pro:wght@200;300;400;500&family=Roboto:wght@500&display=swap">
<style>
  :root {
    --page: #e8e8e8;
    --card: #93c3c2;
    --white: #ffffff;
    --ink: #3b2a30;
    --photo-top: #c9a48a;
    --photo-mid: #e9ece9;
    --photo-low: #2f3b3b;
  }
  * { margin: 0; padding: 0; box-sizing: border-box; }
  html, body { width: 1200px; height: 1155px; overflow: hidden; background: var(--page); }
  .canvas { position: relative; width: 1200px; height: 1155px; }
  .card {
    position: absolute; left: 218px; width: 758px; height: 434px;
    background: var(--card); border-radius: 34px; overflow: hidden;
    box-shadow: 0 6px 10px rgba(0,0,0,0.18);
  }
  .card--front { top: 134px; }
  .card--back { top: 596px; }

  .front-name {
    position: absolute; left: 0; right: 0; top: 172px;
    text-align: center; color: var(--white);
    font-family: "Advent Pro", sans-serif; font-weight: 300;
    font-size: 80px; line-height: 88px; letter-spacing: 10px;
  }
  .social { position: absolute; top: 370px; left: 310px; display: flex; gap: 13px; }
  .social span { width: 28px; height: 28px; border-radius: 50%; background: var(--white); display: block; }

  .portrait {
    position: absolute; left: 2px; top: 16px; width: 260px; height: 418px;
    background: linear-gradient(180deg, var(--photo-top) 0%, var(--photo-mid) 30%, var(--photo-mid) 66%, var(--photo-low) 74%, var(--photo-low) 100%);
    border-radius: 90px 90px 0 0;
  }
  .brand { position: absolute; right: 42px; top: 44px; display: flex; align-items: center; gap: 26px; }
  .brand-dot { width: 84px; height: 84px; border: 2px solid var(--white); border-radius: 50%; }
  .brand-name {
    color: var(--white); font-family: "Advent Pro", sans-serif; font-weight: 300;
    font-size: 64px; line-height: 64px; letter-spacing: 7px;
  }
  .details { position: absolute; right: 42px; top: 192px; text-align: right; color: var(--white); }
  .person-name { font-family: "Roboto", sans-serif; font-weight: 500; font-size: 25px; line-height: 30px; letter-spacing: 0.5px; }
  .person-role { font-family: "Roboto", sans-serif; font-weight: 500; font-size: 14px; line-height: 18px; letter-spacing: 1px; opacity: 0.9; }
  .address { margin-top: 18px; font-family: "Advent Pro", sans-serif; font-weight: 500; font-size: 21px; line-height: 27px; letter-spacing: 0.5px; }
  .contact { margin-top: 10px; font-family: "Advent Pro", sans-serif; font-weight: 500; font-size: 21px; line-height: 27px; letter-spacing: 0.5px; }
  .contact li { list-style: none; display: flex; justify-content: flex-end; align-items: center; gap: 14px; }
  .contact svg { width: 12px; height: 12px; flex: none; }
</style>
</head>
<body>
<main class="canvas">
  <section class="card card--front" aria-label="Card front">
    <div class="front-name">GLIMORA</div>
    <div class="social" aria-label="Social channels">
      <span></span><span></span><span></span><span></span>
    </div>
  </section>

  <section class="card card--back" aria-label="Card back">
    <div class="portrait" role="img" aria-label="Photo of a young woman in a white lace blouse and dark skirt"></div>
    <div class="brand">
      <span class="brand-dot"></span>
      <span class="brand-name">GLIMORA</span>
    </div>
    <div class="details">
      <p class="person-name">DANA RELVIK</p>
      <p class="person-role">OWNER</p>
      <p class="address">48 Palm Row<br>Seaview, FL 30012</p>
      <ul class="contact">
        <li>555.010.2746
          <svg viewBox="0 0 12 12"><path d="M3 1 L5 1 L5.5 3.5 L4.3 4.3 Q5 7 7.7 7.7 L8.5 6.5 L11 7 L11 9 Q11 11 9 11 Q1 10 1 3 Q1 1 3 1 Z" fill="#fff"/></svg>
        </li>
        <li>info@glimora-example.com
          <svg viewBox="0 0 12 12"><rect x="1" y="2.5" width="10" height="7" fill="none" stroke="#fff" stroke-width="1.3"/><path d="M1 3 L6 7 L11 3" fill="none" stroke="#fff" stroke-width="1.3"/></svg>
        </li>
        <li>www.glimora-example.com
          <svg viewBox="0 0 12 12"><circle cx="6" cy="6" r="5" fill="none" stroke="#fff" stroke-width="1.2"/><ellipse cx="6" cy="6" rx="2.2" ry="5" fill="none" stroke="#fff" stroke-width="1"/><path d="M1 6 H11" stroke="#fff" stroke-width="1"/></svg>
        </li>
      </ul>
    </div>
  </section>
</main>
</body>
</html>
```